Ward Compass Business Card Design*

We need a business card design for our company Ward Compass. Our company is specialized in providing online consulting services regarding medical institutions, hospitals and doctors. We work with patients worldwide looking to choose between healthcare providers. We have a website you may use as a reference, where we list doctors and clinics worldwide. So we target Medical providers as well as patients worldwide.
Target Market(s)
Medical Providers and patients around the world
Industry/Entity Type
Medical
Contact Information for Business Card
Salwa Kettani
CEO
+90 612 348 2175
info@wardcompass.example
www.wardcompass.example
14 Annakhil 7 H.R.B. Rabat, Morocco
Requirements
Must have
- Company logo/name on one full side, personal info and smaller logo and company name on the other side.
Nice to have
- Smart and elegant design

```html
<!DOCTYPE html>
<html lang="en">
<head>
<meta charset="utf-8">
<title>Ward Compass Business Card</title>
<link rel="stylesheet" href="https://fonts.googleapis.com/css2?family=Montserrat:wght@600&family=Open+Sans:wght@400;700&display=swap">
<style>
  :root {
    --navy: #1f3f6e;
    --grey: #7c7c7e;
    --ink: #2b2b2b;
    --card: #ffffff;
    --backdrop: #e6e7ea;
  }
  * { box-sizing: border-box; margin: 0; padding: 0; }
  html, body { width: 1200px; height: 768px; overflow: hidden; }
  body {
    background: var(--backdrop);
    display: flex;
    align-items: center;
    justify-content: center;
    gap: 40px;
    font-family: "Open Sans", Arial, sans-serif;
  }
  .card {
    position: relative;
    width: 540px;
    height: 309px;
    background: var(--card);
    box-shadow: 0 6px 18px rgba(0,0,0,0.15);
    overflow: hidden;
  }
  .brand {
    display: flex;
    align-items: center;
    gap: 12px;
  }
  .brand-dot {
    border-radius: 50%;
    background: var(--navy);
    flex: none;
  }
  .brand-name {
    font-family: "Montserrat", Arial, sans-serif;
    font-weight: 600;
    color: var(--navy);
    text-transform: uppercase;
    letter-spacing: 0.04em;
  }

  /* Logo side */
  .card-back .brand {
    position: absolute;
    top: 118px;
    left: 0;
    right: 0;
    justify-content: center;
  }
  .card-back .brand-dot { width: 46px; height: 46px; }
  .card-back .brand-name { font-size: 30px; }
  .card-back .website {
    position: absolute;
    bottom: 34px;
    left: 0;
    right: 0;
    text-align: center;
    font-size: 13px;
    letter-spacing: 0.42em;
    color: var(--ink);
  }

  /* Details side */
  .card-front .accent-circle {
    position: absolute;
    left: -14px;
    top: 46px;
    width: 220px;
    height: 220px;
    border-radius: 50%;
    background: var(--navy);
  }
  .card-front .details {
    position: absolute;
    right: 30px;
    top: 40px;
    text-align: right;
  }
  .card-front .brand { justify-content: flex-end; }
  .card-front .brand-name { font-size: 22px; }
  .person-name {
    margin-top: 26px;
    font-weight: 700;
    font-size: 20px;
    color: var(--navy);
  }
  .person-role {
    font-size: 14px;
    color: var(--grey);
    line-height: 1.1;
  }
  .address {
    margin-top: 12px;
    font-size: 14px;
    line-height: 1.3;
    color: var(--ink);
  }
  .contact-list {
    list-style: none;
    margin-top: 10px;
    font-size: 14px;
    color: var(--ink);
  }
  .contact-list li {
    display: flex;
    align-items: center;
    justify-content: flex-end;
    gap: 10px;
    line-height: 1.45;
  }
  .contact-list svg { width: 14px; height: 14px; fill: var(--navy); flex: none; }
</style>
</head>
<body>

  <section class="card card-back" aria-label="Business card, logo side">
    <div class="brand">
      <span class="brand-dot"></span>
      <span class="brand-name">Ward Compass</span>
    </div>
    <p class="website">www.wardcompass.example</p>
  </section>

  <section class="card card-front" aria-label="Business card, contact side">
    <div class="accent-circle"></div>
    <div class="details">
      <div class="brand">
        <span class="brand-name">Ward Compass</span>
      </div>
      <p class="person-name">Salwa Kettani</p>
      <p class="person-role">CEO</p>
      <p class="address">14 Annakhil 7<br>H.R.B. Rabat, Morocco</p>
      <ul class="contact-list">
        <li>+90 612 348 2175
          <svg viewBox="0 0 24 24" aria-hidden="true"><path d="M6.6 10.8a15.1 15.1 0 0 0 6.6 6.6l2.2-2.2a1 1 0 0 1 1-.25 11.4 11.4 0 0 0 3.6.57 1 1 0 0 1 1 1V20a1 1 0 0 1-1 1A17 17 0 0 1 3 4a1 1 0 0 1 1-1h3.5a1 1 0 0 1 1 1c0 1.25.2 2.45.57 3.57a1 1 0 0 1-.25 1z"/></svg>
        </li>
        <li>info@wardcompass.example
          <svg viewBox="0 0 24 24" aria-hidden="true"><path d="M2 5h20v14H2z M2 5l10 8 10-8" fill="none" stroke="#1f3f6e" stroke-width="2.4"/></svg>
        </li>
        <li>www.wardcompass.example
          <svg viewBox="0 0 24 24" aria-hidden="true"><circle cx="12" cy="12" r="9" fill="none" stroke="#1f3f6e" stroke-width="2.4"/><path d="M3 12h18M12 3c3 3 3 15 0 18M12 3c-3 3-3 15 0 18" fill="none" stroke="#1f3f6e" stroke-width="1.8"/></svg>
        </li>
      </ul>
    </div>
  </section>

</body>
</html>
```